Start up Events company needs a business card design

We are a brand new start up events company that need an impressively designed business card to make the best first impression with our future clients.

Description on company:
- start-up company
- in the events management industry
- selling flagship children related event
- our future clients will mostly be vendors in the alternative education industry. dance schools, music schools, sports camp facilitators, academic establishments
- our target market are kids, parents of kids, mass market

What we need in the business card:
- we currently have a rough design that I have uploaded. we need to brush it up. make it look more professional, more vibrant but keep the meaning of the company which is called "Lantern & Kite"
- a reason for the "Lantern & Kite" concept is because we will be starting off with a flagship event & be branching out into all other related businesses relating to our core highlight which is kids & alternative education.
- this is a tentative logo we have selected - which is a girl on a swing. to represent momentum as a start up company and related to children
- if you have a better logo alternative, please do suggest it to us
- we need more colours, vibrancy yet it has to be sleek and professional.

As we are a start-up company, our budget is tight. If you have a good idea / concept, do take on this project overlooking the tight budget.
If you require any additional information, do feel free to drop us messages!

Thank you designers!

```html
<!DOCTYPE html>
<html lang="en">
<head>
<meta charset="utf-8">
<title>Lantern &amp; Kite — Business Card</title>
<link rel="stylesheet" href="https://fonts.googleapis.com/css2?family=Open+Sans:wght@300;400;600;700&display=swap">
<style>
  :root {
    --backdrop: #a3a3a3;
    --card: #ffffff;
    --ink: #2b2b2b;
    --ink-soft: #4a4a4a;
    --ink-muted: #7a7a7a;
    --band-dark: #0e0e0e;
    --band-light: #dcdcdc;
    --accent: #b3139f;
    --on-dark: #ffffff;
  }
  * { box-sizing: border-box; margin: 0; padding: 0; }
  html, body {
    width: 1200px; height: 894px; overflow: hidden;
    background: var(--backdrop);
    font-family: "Open Sans", Arial, sans-serif;
  }
  .canvas { position: relative; width: 1200px; height: 894px; }

  .card {
    position: absolute;
    width: 560px; height: 320px;
    background: var(--card);
    border-radius: 4px;
    box-shadow: 0 6px 18px rgba(0,0,0,0.18);
    overflow: hidden;
  }
  .card--back  { left: 600px; top: 110px; }
  .card--front { left: 40px;  top: 460px; }

  .brand { position: absolute; display: flex; flex-direction: column; }
  .brand__row { display: flex; align-items: center; gap: 8px; }
  .brand__dot { width: 12px; height: 12px; border-radius: 50%; background: var(--ink); }
  .brand__name {
    font-weight: 700; font-size: 18px; color: var(--ink);
    letter-spacing: 0.5px; text-transform: uppercase;
  }
  .brand__tagline {
    font-size: 9px; color: var(--ink-muted); font-weight: 400;
    margin-left: 20px; margin-top: 1px;
  }
  .card--back .brand  { left: 190px; top: 120px; }
  .card--front .brand { left: 150px; top: 60px; }

  .web-band {
    position: absolute; left: 0; top: 238px;
    width: 270px; height: 36px;
    background: var(--band-light);
    border-radius: 0 18px 18px 0;
    display: flex; align-items: center; padding-left: 26px;
    font-size: 15px; font-weight: 600; color: var(--ink-soft);
    letter-spacing: 0.5px;
  }

  .person { position: absolute; left: 40px; top: 122px; white-space: nowrap; }
  .person__name { font-size: 25px; font-weight: 600; color: var(--ink-soft); }
  .person__sep  { font-size: 25px; font-weight: 600; color: var(--ink-soft); margin: 0 6px; }
  .person__role { font-size: 17px; font-weight: 300; color: var(--ink-soft); }

  .address {
    position: absolute; left: 40px; top: 166px;
    font-size: 14px; font-weight: 700; color: var(--ink);
  }

  .contact-band {
    position: absolute; left: 0; top: 200px;
    width: 470px; height: 36px;
    background: var(--band-dark);
    border-radius: 0 18px 18px 0;
    display: flex; align-items: center; gap: 18px; padding-left: 18px;
    color: var(--on-dark); font-size: 13px;
    white-space: nowrap;
  }
  .contact { display: flex; align-items: center; gap: 6px; }
  .contact__icon { width: 16px; height: 16px; flex: none; }
</style>
</head>
<body>
<main class="canvas">

  <section class="card card--back" aria-label="Business card, back">
    <div class="brand">
      <div class="brand__row">
        <span class="brand__dot"></span>
        <span class="brand__name">Lantern &amp; Kite</span>
      </div>
      <span class="brand__tagline">Events for kids</span>
    </div>
    <div class="web-band">www.lanternkite.com</div>
  </section>

  <section class="card card--front" aria-label="Business card, front">
    <div class="brand">
      <div class="brand__row">
        <span class="brand__dot"></span>
        <span class="brand__name">Lantern &amp; Kite</span>
      </div>
      <span class="brand__tagline">Events for kids</span>
    </div>

    <div class="person">
      <span class="person__name">Daniel Rowe</span><span class="person__sep">|</span><span class="person__role">President &amp; CEO</span>
    </div>
    <p class="address">27, 4th floor, Harbour Lane Road</p>

    <div class="contact-band">
      <span class="contact">
        <svg class="contact__icon" viewBox="0 0 16 16" aria-hidden="true">
          <circle cx="8" cy="8" r="8" fill="var(--accent)"/>
          <path d="M5.2 4.2l1.4-.3.8 1.9-.9.7c.4.9 1.1 1.6 2 2l.7-.9 1.9.8-.3 1.4c-3 .2-5.8-2.6-5.6-5.6z" fill="#fff"/>
        </svg>
        010 555 0142
      </span>
      <span class="contact">
        <svg class="contact__icon" viewBox="0 0 16 16" aria-hidden="true">
          <circle cx="8" cy="8" r="8" fill="var(--accent)"/>
          <path d="M5.2 4.2l1.4-.3.8 1.9-.9.7c.4.9 1.1 1.6 2 2l.7-.9 1.9.8-.3 1.4c-3 .2-5.8-2.6-5.6-5.6z" fill="#fff"/>
        </svg>
        010 555 0142
      </span>
      <span class="contact">
        <svg class="contact__icon" viewBox="0 0 16 16" aria-hidden="true">
          <circle cx="8" cy="8" r="8" fill="var(--accent)"/>
          <rect x="4" y="5" width="8" height="6" rx="0.6" fill="#fff"/>
          <path d="M4.3 5.4L8 8.3l3.7-2.9" fill="none" stroke="var(--accent)" stroke-width="0.9"/>
        </svg>
        hello@lanternkite.com
      </span>
    </div>
  </section>

</main>
</body>
</html>
```